Business card design for my company.
I would like the card's background colour to be black. You can also see our web site to get an idea of our brand. https://www.tmwhomecrafting.com.au/
- Name
- Email

```html
<!DOCTYPE html>
<html lang="en">
<head>
<meta charset="utf-8">
<title>TMW Home Crafting – Business Card</title>
<link href="https://fonts.googleapis.com/css2?family=Montserrat:wght@400;500;700&display=swap" rel="stylesheet">
<style>
  :root {
    --page-bg: #2b2b2d;
    --card-black: #1c1c1d;
    --card-deep: #0d0d0e;
    --pattern-light: #6a6a6c;
    --brand-green: #1e9a3f;
    --text-white: #f2f2f2;
  }
  * { margin: 0; padding: 0; box-sizing: border-box; }
  html, body { width: 1200px; height: 874px; overflow: hidden; }
  body {
    background: var(--page-bg);
    font-family: "Montserrat", sans-serif;
    position: relative;
  }
  .card {
    position: absolute;
    left: 250px;
    width: 700px;
    height: 400px;
    border-radius: 22px;
    overflow: hidden;
  }
  .card-back { top: 17px; background: var(--card-deep); }
  .card-front { top: 447px; background: var(--card-black); }

  .back-pattern {
    position: absolute; inset: 0;
    background: linear-gradient(125deg, var(--pattern-light) 0%, #2a2a2c 45%, var(--card-deep) 75%);
  }
  .back-brand {
    position: absolute;
    left: 50%; top: 50%;
    transform: translate(-50%, -50%);
    display: flex; align-items: center; gap: 8px;
    color: var(--text-white);
    font-weight: 700; font-size: 15px;
    white-space: nowrap;
  }
  .brand-square { width: 12px; height: 12px; background: var(--brand-green); }

  .front-brand {
    position: absolute;
    left: 48px; top: 150px;
    width: 260px;
    display: flex; align-items: center; gap: 14px;
    color: var(--text-white);
    font-weight: 700; font-size: 30px; line-height: 1.15;
  }
  .front-brand .brand-square { width: 22px; height: 22px; flex: none; }

  .divider {
    position: absolute;
    left: 340px; top: 130px;
    width: 2px; height: 180px;
    background: var(--brand-green);
  }
  .contact-block { position: absolute; left: 368px; top: 140px; color: var(--text-white); }
  .person-name { color: var(--brand-green); font-weight: 700; font-size: 30px; line-height: 1; }
  .person-role { font-weight: 500; font-size: 17px; margin-top: 8px; }
  .contact-list { list-style: none; margin-top: 20px; }
  .contact-list li {
    display: flex; align-items: center; gap: 10px;
    font-size: 17px; font-weight: 500; height: 32px;
  }
  .contact-list svg { width: 16px; height: 16px; fill: var(--brand-green); flex: none; }
</style>
</head>
<body>

<section class="card card-back">
  <div class="back-pattern" role="img" aria-label="Repeating brand pattern with glossy fade across the card back"></div>
  <div class="back-brand"><span class="brand-square"></span>TMW Home Crafting</div>
</section>

<section class="card card-front">
  <div class="front-brand"><span class="brand-square"></span><span>TMW Home Crafting</span></div>
  <div class="divider"></div>
  <div class="contact-block">
    <p class="person-name">Daniel Hartley</p>
    <p class="person-role">General Manager</p>
    <ul class="contact-list">
      <li>
        <svg viewBox="0 0 16 16"><path d="M3 1h3l1.5 4-2 1.3a9 9 0 0 0 4.2 4.2L11 8.5l4 1.5v3a2 2 0 0 1-2 2A12 12 0 0 1 1 3a2 2 0 0 1 2-2z"/></svg>
        0400 123 456
      </li>
      <li>
        <svg viewBox="0 0 16 16"><path d="M1 3h14v1.2L8 9 1 4.2z"/><path d="M1 5.8l7 4.8 7-4.8V13H1z"/></svg>
        info@tmwhomecrafting.com.au
      </li>
      <li>
        <svg viewBox="0 0 16 16"><path d="M8 1a7 7 0 1 0 0 14A7 7 0 0 0 8 1zm0 1.5c.9 0 1.9 1.7 2.2 4.5H5.8C6.1 4.2 7.1 2.5 8 2.5zM2.6 8.8h2.1c.1 1.7.5 3.1 1 4.1A5.5 5.5 0 0 1 2.6 8.8zm0-1.6a5.5 5.5 0 0 1 3.1-4.1c-.5 1-.9 2.4-1 4.1zm5.4 6.3c-.9 0-1.9-1.7-2.2-4.7h4.4c-.3 3-1.3 4.7-2.2 4.7zm2.3-.6c.5-1 .9-2.4 1-4.1h2.1a5.5 5.5 0 0 1-3.1 4.1zm1-5.7c-.1-1.7-.5-3.1-1-4.1a5.5 5.5 0 0 1 3.1 4.1z"/></svg>
        www.tmwhomecrafting.com.au
      </li>
    </ul>
  </div>
</section>

</body>
</html>
```